BrindleStaffing Business Card Design

We are a staffing company finding positions for dedicated nurses and physicians.

Target Market(s)

Business Professionals

Industry/Entity Type

Staffing

Contact Information for Business Card

Gordon Pratley
Chairman
417 39th Avenue South
SAINT PETERSBURG FL 33712
813-555-4172 Mobile
813-555-8036 Fax
gpratley@brindlestaffing.com
www.brindlestaffing.com

Font styles to use
Sans Serif

Colors
fbee3e
f04a50
f37122

Requirements
Must have
• Logo Attached, see colors below. We'd like to see Yellow, Orange and Red.

```html
<!DOCTYPE html>
<html lang="en">
<head>
<meta charset="utf-8">
<title>BrindleStaffing Business Card</title>
<link href="https://fonts.googleapis.com/css2?family=Open+Sans:wght@400;600;700&display=swap" rel="stylesheet">
<style>
  :root {
    --backdrop: #1c1c1e;
    --card-white: #ffffff;
    --brand-red: #f04a50;
    --brand-orange: #f37122;
    --brand-yellow: #fbee3e;
    --ink-dark: #2b2b2b;
    --ink-light: #ffffff;
  }
  * { box-sizing: border-box; margin: 0; padding: 0; }
  html, body {
    width: 1200px; height: 960px; overflow: hidden;
    background: var(--backdrop);
    font-family: "Open Sans", sans-serif;
  }
  .canvas { position: relative; width: 1200px; height: 960px; }

  .card {
    position: absolute;
    width: 680px; height: 388px;
    background: var(--card-white);
    box-shadow: 0 14px 30px rgba(0,0,0,.45);
    overflow: hidden;
  }

  /* Front card */
  .card-front { left: 440px; top: 70px; }
  .card-front .wordmark {
    position: absolute; left: 0; right: 0; top: 128px;
    text-align: center;
    font-size: 64px; font-weight: 700; letter-spacing: -1px;
    color: var(--brand-red);
  }
  .card-front .web {
    position: absolute; left: 0; right: 0; top: 224px;
    text-align: center;
    font-size: 20px; letter-spacing: 2px;
    color: var(--ink-dark);
  }

  /* Back card */
  .card-back { left: 80px; top: 500px; }
  .card-back .logo-side {
    position: absolute; left: 0; top: 0; width: 316px; height: 100%;
    display: flex; align-items: center; justify-content: center;
  }
  .card-back .wordmark {
    font-size: 36px; font-weight: 700; letter-spacing: -0.5px;
    color: var(--brand-red);
  }
  .card-back .divider {
    position: absolute; left: 316px; top: 0; width: 4px; height: 100%;
    background: var(--brand-yellow);
  }
  .card-back .contact-panel {
    position: absolute; left: 320px; top: 0; right: 0; bottom: 0;
    background: var(--brand-orange);
    color: var(--ink-light);
    padding: 34px 30px 0 36px;
    font-size: 18px; line-height: 1.38;
  }
  .contact-panel .person { font-size: 23px; font-weight: 700; }
  .contact-panel .role { margin-bottom: 16px; }
  .contact-panel .address { margin-bottom: 12px; }
  .contact-panel .line { display: flex; align-items: center; gap: 10px; }
  .contact-panel .line svg { width: 16px; height: 16px; flex: none; }
</style>
</head>
<body>
<div class="canvas">

  <section class="card card-front">
    <div class="wordmark">BrindleStaffing</div>
    <div class="web">www.brindlestaffing.com</div>
  </section>

  <section class="card card-back">
    <div class="logo-side">
      <div class="wordmark">BrindleStaffing</div>
    </div>
    <div class="divider"></div>
    <div class="contact-panel">
      <div class="person">Gordon Pratley</div>
      <div class="role">Chairman</div>
      <div class="address">417 39th Avenue South<br>Saint petersburg fl 33712</div>
      <div class="line">
        <svg viewBox="0 0 16 16" aria-hidden="true"><circle cx="8" cy="8" r="7" fill="none" stroke="#fff" stroke-width="1.3"/><path d="M5.5 4.5l1.5 2-1 1c.6 1.2 1.4 2 2.5 2.5l1-1 2 1.5-1 1.5c-3 0-6-3-6-6z" fill="#fff"/></svg>
        <span>813-555-4172 Mobile</span>
      </div>
      <div class="line">
        <svg viewBox="0 0 16 16" aria-hidden="true"><rect x="4" y="1.5" width="8" height="4" fill="none" stroke="#fff" stroke-width="1.2"/><rect x="1.5" y="5.5" width="13" height="6" rx="1" fill="#fff"/><rect x="4" y="10" width="8" height="4.5" fill="#fff" stroke="#f37122" stroke-width="1"/></svg>
        <span>813-555-8036 Fax</span>
      </div>
      <div class="line">
        <svg viewBox="0 0 16 16" aria-hidden="true"><rect x="1.5" y="3.5" width="13" height="9" rx="1" fill="#fff"/><path d="M2 4l6 5 6-5" fill="none" stroke="#f37122" stroke-width="1.3"/></svg>
        <span>gpratley@brindlestaffing.com</span>
      </div>
      <div class="line">
        <svg viewBox="0 0 16 16" aria-hidden="true"><circle cx="8" cy="8" r="6.5" fill="none" stroke="#fff" stroke-width="1.3"/><ellipse cx="8" cy="8" rx="2.8" ry="6.5" fill="none" stroke="#fff" stroke-width="1.1"/><path d="M1.5 8h13M2.5 5h11M2.5 11h11" stroke="#fff" stroke-width="1"/></svg>
        <span>www.brindlestaffing.com</span>
      </div>
    </div>
  </section>

</div>
</body>
</html>
```